RWT Fittings Ltd Business Cards

We need a business card with our business logo. We provide window and door installations on high-rises in west coast British Colombia, Canada.

I would like my business information and details on one side of the card, and the other side the company name with logo

Target Market(s)

General Contractors

Industry/Entity Type

Construction

Contact Information for Business Card

one side i want my company name and logo in the dark theme logo that i provided

Requirements
Must have
• Marco Peltieri, 16045518293, RWTFittings@mailbox-demo.com, 1407-5194 Linden Row Burnaby BC, V5H 2K9, Owner & Manager

```html
<!DOCTYPE html>
<html lang="en">
<head>
<meta charset="utf-8">
<title>RWT Fittings Ltd — Business Cards</title>
<link rel="stylesheet" href="https://fonts.googleapis.com/css2?family=Roboto:wght@400;500;700&display=swap">
<style>
  :root {
    --stage: #232323;
    --card: #1f1f22;
    --panel-dark: #0d0d0f;
    --panel-mid: #2a2a2d;
    --accent: #29a8e0;
    --grey: #9a9a9a;
    --white: #f2f2f2;
    --photo-dark: #2b2824;
    --photo-light: #5a544c;
  }
  * { box-sizing: border-box; margin: 0; padding: 0; }
  html, body { width: 1200px; height: 780px; overflow: hidden; }
  body {
    background: var(--stage);
    font-family: "Roboto", Arial, sans-serif;
    display: flex;
    align-items: center;
    justify-content: center;
    gap: 40px;
  }
  .card {
    position: relative;
    width: 540px;
    height: 309px;
    overflow: hidden;
    box-shadow: 0 18px 40px rgba(0,0,0,.55);
  }

  /* Contact side */
  .card--contact { background: var(--card); }
  .contact__panel {
    position: absolute;
    inset: 0;
    width: 100%;
    height: 100%;
  }
  .contact__body {
    position: absolute;
    left: 268px;
    top: 34px;
    right: 24px;
  }
  .brand-name {
    display: flex;
    align-items: center;
    gap: 10px;
    font-weight: 700;
    font-size: 22px;
    color: var(--accent);
    letter-spacing: .5px;
  }
  .brand-name__mark {
    width: 14px;
    height: 14px;
    background: var(--accent);
  }
  .person { margin-top: 34px; }
  .person__name {
    font-weight: 700;
    font-size: 26px;
    line-height: 1;
  }
  .person__first { color: var(--accent); }
  .person__last { color: var(--grey); }
  .person__role {
    margin-top: 6px;
    font-weight: 500;
    font-size: 13px;
    color: var(--white);
  }
  .details {
    margin-top: 18px;
    font-size: 12.5px;
    line-height: 1.5;
    color: var(--white);
    list-style: none;
  }
  .details__item { display: flex; align-items: center; gap: 8px; }
  .details__icon { width: 12px; height: 12px; flex: none; }
  .details__address { margin-bottom: 6px; padding-left: 20px; }
  .accent-bar {
    position: absolute;
    right: 0;
    bottom: 54px;
    width: 12px;
    height: 56px;
    background: var(--accent);
  }

  /* Brand side */
  .card--brand {
    background: linear-gradient(125deg, var(--photo-dark) 0%, #3a3630 45%, var(--photo-light) 100%);
    display: flex;
    align-items: center;
    justify-content: center;
  }
  .brand-photo { position: absolute; inset: 0; }
  .card--brand .brand-name {
    position: relative;
    font-size: 30px;
  }
  .card--brand .brand-name__mark { width: 18px; height: 18px; }
</style>
</head>
<body>

  <section class="card card--contact" aria-label="Business card, contact side">
    <svg class="contact__panel" viewBox="0 0 540 309" aria-hidden="true">
      <defs>
        <linearGradient id="panelShade" x1="0" y1="0" x2="1" y2="0.3">
          <stop offset="0" stop-color="#0b0b0d"/>
          <stop offset="1" stop-color="#2c2c30"/>
        </linearGradient>
      </defs>
      <polygon points="0,0 250,0 190,309 0,309" fill="url(#panelShade)"/>
    </svg>

    <div class="contact__body">
      <div class="brand-name"><span class="brand-name__mark"></span>RWT Fittings Ltd</div>

      <div class="person">
        <p class="person__name"><span class="person__first">Marco</span> <span class="person__last">Peltieri</span></p>
        <p class="person__role">Owner &amp; Manager</p>
      </div>

      <ul class="details">
        <li class="details__address">1407-5194 Linden Row<br>Burnaby BC, V5H 2K9</li>
        <li class="details__item">
          <svg class="details__icon" viewBox="0 0 24 24" aria-hidden="true"><path fill="#29a8e0" d="M6.6 10.8a15.1 15.1 0 0 0 6.6 6.6l2.2-2.2a1 1 0 0 1 1-.25 11.4 11.4 0 0 0 3.6.57 1 1 0 0 1 1 1V20a1 1 0 0 1-1 1A17 17 0 0 1 3 4a1 1 0 0 1 1-1h3.5a1 1 0 0 1 1 1c0 1.25.2 2.45.57 3.57a1 1 0 0 1-.25 1z"/></svg>
          1 604 551 8293
        </li>
        <li class="details__item">
          <svg class="details__icon" viewBox="0 0 24 24" aria-hidden="true"><path fill="#29a8e0" d="M3 5h18a1 1 0 0 1 1 1v12a1 1 0 0 1-1 1H3a1 1 0 0 1-1-1V6a1 1 0 0 1 1-1zm9 7.5L4 7v10h16V7z"/></svg>
          RWTFittings@mailbox-demo.com
        </li>
      </ul>
    </div>
    <span class="accent-bar"></span>
  </section>

  <section class="card card--brand" aria-label="Business card, brand side">
    <div class="brand-photo" role="img" aria-label="Softly blurred photograph of a dim modern interior with a potted plant"></div>
    <div class="brand-name"><span class="brand-name__mark"></span>RWT Fittings Ltd</div>
  </section>

</body>
</html>
```